Wandering Rooms Stationary Set

Wandering Rooms is a bespoke interior design firm set to provide services to VIP clients with elegance and minimalism is the main theme for our stationary set. We require a full stationary set covering A4 letterhead, A4 & A3 envelopes, business cards, USB's, CDs, email signature and any other item the designer sees fit. logo is already designed and finalized, and we require the designer to use it as is without modifying the logo.

Address to be used on letterhead / business cards ...etc shall be as follows:

Phone : +971 2 518 2047
P.O. Box : 309186
Address: Block C&D, Bldg. 47, Court 12, Abu Dhabi, United Arab Emirates
Website: www.wanderingrooms-example.com

Target Market(s)

VIP Clients

Industry/Entity Type

Interior Design

Font styles to use
Other font styles liked:
• something to be unique

Colors

Designer to choose colors to be used in the design.

Requirements
Must have
• Elegant, minimalistic
Nice to have
• Simple yet elegant design having a sharp yet clean cut format
Should not have
• No additional colours, just colours that are used in the logo (silver, black or gold)

```html
<!DOCTYPE html>
<html lang="en">
<head>
<meta charset="utf-8">
<title>Wandering Rooms – Business Card</title>
<link rel="stylesheet" href="https://fonts.googleapis.com/css2?family=Cormorant+Garamond:wght@500&family=Arimo:wght@400;700&display=swap">
<style>
  :root {
    --backdrop: #7b7b7b;
    --card: #4a4a4a;
    --gold: #cdb57c;
    --gold-soft: #bfa772;
  }
  html, body {
    margin: 0;
    padding: 0;
    overflow: hidden;
  }
  body {
    width: 1200px;
    height: 1017px;
    background: var(--backdrop);
    position: relative;
  }
  .card {
    position: absolute;
    left: 340px;
    width: 548px;
    height: 356px;
    background: var(--card);
    box-sizing: border-box;
  }
  .card--front { top: 106px; }
  .card--back  { top: 548px; }

  .brand-name {
    position: absolute;
    left: 0;
    right: 0;
    top: 150px;
    margin: 0;
    text-align: center;
    font-family: "Cormorant Garamond", serif;
    font-weight: 500;
    font-size: 38px;
    letter-spacing: 1px;
    color: var(--gold);
  }

  .contact {
    position: absolute;
    left: 0;
    right: 0;
    top: 101px;
    text-align: center;
    font-family: "Arimo", sans-serif;
    color: var(--gold-soft);
    font-size: 13.5px;
    line-height: 17px;
  }
  .contact p { margin: 0; }
  .contact__name {
    font-weight: 700;
    font-size: 16px;
    letter-spacing: 0.5px;
    color: var(--gold);
    text-transform: uppercase;
    line-height: 20px;
  }
  .contact__role { margin-bottom: 19px !important; }
  .contact__lines { margin-bottom: 21px !important; }
</style>
</head>
<body>
  <section class="card card--front">
    <h1 class="brand-name">Wandering Rooms</h1>
  </section>

  <section class="card card--back">
    <div class="contact">
      <p class="contact__name">Jordan Halvers</p>
      <p class="contact__role">General Manager</p>
      <div class="contact__lines">
        <p>Tel: +971 2 518 2047</p>
        <p>www.wanderingrooms-example.com</p>
      </div>
      <p>Block C&amp;D, Bldg. 47, Court 12</p>
      <p>Abu Dhabi, United Arab Emirates</p>
    </div>
  </section>
</body>
</html>
```